Laser Tattoo Removal Business Cards

We are looking for a professional business card design for a laser tattoo removal business. Ideally looking for a black business card design. The name of the business is Brightline Tattoo Removal. We place our cards at local tattoo shops so we ideally are looking for something trendy/edgy to draw both male and female clientele in.

Target Market(s)

Male/Female ages 18-60

Contact Information for Business Card

black background ideally.. hoping to stay within greys, whites and black

Font styles to use
Serif
Sans Serif

Colors
121212
a9a9a9
5c5c5c
f5f5f5
ffffff
7f7f7f
606060
848484
9d9d9d

Requirements
Must have
• Employee Info:
• Melissa Thornbury
• Chief Executive Offer
• m: 919.537.2846
• w: 919.362.4178
• f: 919.685.3907
• mthornbury@brightlinetattooremoval.example
• Address:
• 4615 Oakmere Pkwy, Suite 210
• Raleigh, NC 27654
• Website:
• www.brightlinetattooremoval.example
Nice to have
• Myabe business name on back or logo on back and employee info on the front

```html
<!DOCTYPE html>
<html lang="en">
<head>
<meta charset="UTF-8">
<title>Brightline Tattoo Removal – Business Card</title>
<link href="https://fonts.googleapis.com/css2?family=Oswald:wght@400&family=Roboto:wght@400;500&display=swap" rel="stylesheet">
<style>
  :root {
    --backdrop: #9a9a9a;
    --ink-black: #121212;
    --panel-grey: #d6d6d8;
    --swoosh-grey: #7f7f7f;
    --text-dark: #3a3a3a;
    --brand-dark: #2a2a2a;
    --brand-silver: #a9a9a9;
    --text-light: #f5f5f5;
    --white: #ffffff;
  }
  * { margin: 0; padding: 0; box-sizing: border-box; }
  html, body {
    width: 1105px; height: 1200px; overflow: hidden;
    background: var(--backdrop);
    font-family: "Roboto", Arial, sans-serif;
  }
  .canvas { position: relative; width: 1105px; height: 1200px; }
  .card {
    position: absolute; left: 182px; width: 746px; height: 427px;
    overflow: hidden; background: var(--ink-black);
  }
  .card--front { top: 119px; }
  .card--back { top: 637px; }

  .front-shape { position: absolute; inset: 0; width: 100%; height: 100%; }

  .person { position: absolute; left: 44px; top: 38px; color: var(--white); }
  .person__name { font-size: 22px; font-weight: 500; letter-spacing: 0.3px; line-height: 1.1; }
  .person__title { font-size: 17px; font-weight: 400; margin-top: 3px; }

  .brand {
    position: absolute; text-align: center;
    font-family: "Oswald", "Arial Narrow", sans-serif; font-weight: 400;
    text-transform: uppercase; line-height: 1.15;
  }
  .brand__line--main { font-size: 46px; letter-spacing: 3px; }
  .brand__line--sub { font-size: 22px; letter-spacing: 5px; margin-top: 8px; }
  .card--front .brand { left: 440px; top: 128px; width: 290px; color: var(--brand-dark); }
  .card--back .brand { left: 0; width: 100%; top: 135px; color: var(--brand-silver); }
  .card--back .brand__line--main { font-size: 62px; letter-spacing: 5px; }
  .card--back .brand__line--sub { font-size: 26px; letter-spacing: 7px; }

  .contact {
    position: absolute; left: 44px; top: 316px;
    color: var(--text-dark); font-size: 16px; line-height: 25px;
  }
  .contact__label { font-weight: 500; color: var(--ink-black); }

  .website {
    position: absolute; left: 0; width: 100%; top: 364px; text-align: center;
    color: var(--text-light); font-size: 17px; letter-spacing: 2.6px;
  }
</style>
</head>
<body>
<main class="canvas">

  <section class="card card--front" aria-label="Business card front">
    <svg class="front-shape" viewBox="0 0 540 309" preserveAspectRatio="none" aria-hidden="true">
      <path d="M0 150 C 120 95, 300 62, 540 56 L540 62 C 300 70, 120 105, 0 168 Z" fill="var(--swoosh-grey)"/>
      <path d="M0 170 C 130 110, 300 70, 540 62 L540 309 L0 309 Z" fill="var(--panel-grey)"/>
    </svg>

    <div class="person">
      <p class="person__name">MELISSA THORNBURY</p>
      <p class="person__title">Chief Executive Offer</p>
    </div>

    <div class="brand">
      <p class="brand__line--main">Brightline</p>
      <p class="brand__line--sub">Tattoo Removal</p>
    </div>

    <address class="contact" style="font-style:normal">
      <p>4615 Oakmere Pkwy, Suite 210, Raleigh, NC 27654</p>
      <p><span class="contact__label">P</span> : 919.362.4178 &nbsp;<span class="contact__label">C</span> : 919.537.2846 &nbsp;<span class="contact__label">F</span> : 919.685.3907</p>
      <p>mthornbury@brightlinetattooremoval.example | www.brightlinetattooremoval.example</p>
    </address>
  </section>

  <section class="card card--back" aria-label="Business card back">
    <div class="brand">
      <p class="brand__line--main">Brightline</p>
      <p class="brand__line--sub">Tattoo Removal</p>
    </div>
    <p class="website">www.brightlinetattooremoval.example</p>
  </section>

</main>
</body>
</html>
```